BOLD & MINIMALIST DESIGN NEEDED

We want a very bold but minimalistic business card design that is impactful and utilizes both sides of the business card. Our current logo is included for your use.

We want bold fonts and good use of negative space. We don't want the logo to overpower the design.

Target Market(s)

Professionals who are building new commercial buildings.

Industry/Entity Type

Construction

Contact Information for Business Card

Name, Title, email, office phone, cell phone, website

Font styles to use
Serif
Sans Serif

Requirements
Must have
• Bold design!

```html
<!DOCTYPE html>
<html lang="en">
<head>
<meta charset="utf-8">
<title>Ridgecrest Design + Build — Business Card</title>
<link rel="stylesheet" href="https://fonts.googleapis.com/css2?family=Marcellus&display=swap">
<style>
  :root {
    --page: #e6e3de;
    --card-top: #ffffff;
    --card-bottom: #e9e9e9;
    --ink: #0b0b0b;
    --text: #2a2a2a;
    --green: #6cc04a;
    --white: #ffffff;
    --rule: #222222;
  }
  * { box-sizing: border-box; margin: 0; padding: 0; }
  html, body { width: 1200px; height: 900px; overflow: hidden; }
  body {
    background: var(--page);
    position: relative;
    font-family: "Marcellus", serif;
    color: var(--text);
  }
  .card {
    position: absolute;
    width: 560px;
    height: 320px;
    background: linear-gradient(160deg, var(--card-top) 0%, var(--card-bottom) 100%);
    box-shadow: 0 10px 24px rgba(0,0,0,0.22);
    overflow: hidden;
  }
  .card--front { left: 320px; top: 90px; }
  .card--back  { left: 320px; top: 480px; }
  .card__band { position: absolute; inset: 0; width: 100%; height: 100%; }

  .brand {
    position: absolute;
    display: flex;
    align-items: center;
    gap: 10px;
    color: var(--ink);
    font-size: 26px;
    letter-spacing: 0.5px;
    line-height: 1;
  }
  .brand__square { width: 18px; height: 18px; background: var(--green); flex: none; }
  .card--front .brand { left: 42px; top: 160px; }
  .card--back .brand { right: 30px; top: 40px; font-size: 20px; }

  .front__web {
    position: absolute;
    left: 62px; bottom: 30px;
    color: var(--green);
    font-size: 15px;
    letter-spacing: 4px;
  }

  .person { position: absolute; left: 40px; top: 150px; }
  .person__name { color: var(--green); font-size: 22px; line-height: 1.1; }
  .person__title { color: var(--ink); font-size: 15px; margin-top: 3px; }
  .person__rule {
    position: absolute;
    left: 110px; top: 185px;
    width: 380px; height: 1px;
    background: var(--rule);
  }

  .contacts { position: absolute; left: 52px; top: 196px; list-style: none; }
  .contacts li {
    display: flex; align-items: center; gap: 10px;
    font-size: 13.5px; line-height: 20px; color: var(--text);
  }
  .contacts svg { width: 13px; height: 13px; flex: none; }

  .address {
    position: absolute;
    left: 40px; bottom: 12px;
    display: flex; align-items: center; gap: 10px;
    color: var(--white);
    font-size: 15px;
  }
  .address svg { width: 12px; height: 16px; }
</style>
</head>
<body>

  <section class="card card--front" aria-label="Card front">
    <svg class="card__band" viewBox="0 0 560 320" preserveAspectRatio="none" aria-hidden="true">
      <path d="M0 258 L360 258 C410 258 420 185 480 178 L560 170 L560 320 L0 320 Z" fill="var(--ink)"/>
    </svg>
    <div class="brand"><span class="brand__square"></span>RIDGECREST DESIGN + BUILD</div>
    <p class="front__web">www.ridgecrest-db.com</p>
  </section>

  <section class="card card--back" aria-label="Card back">
    <svg class="card__band" viewBox="0 0 560 320" preserveAspectRatio="none" aria-hidden="true">
      <path d="M0 285 L380 285 C430 285 440 215 495 205 L560 190 L560 320 L0 320 Z" fill="var(--ink)"/>
    </svg>
    <div class="brand"><span class="brand__square"></span>RIDGECREST DESIGN + BUILD</div>

    <div class="person">
      <p class="person__name">Jonah Whitfield</p>
      <p class="person__title">Founder</p>
    </div>
    <span class="person__rule"></span>

    <ul class="contacts">
      <li>
        <svg viewBox="0 0 12 12" aria-hidden="true"><rect x="3" y="0.5" width="6" height="11" rx="1" fill="none" stroke="var(--green)" stroke-width="1"/></svg>
        3XX-2XX-9XXX
      </li>
      <li>
        <svg viewBox="0 0 12 12" aria-hidden="true"><path d="M2 1 L4.5 1 L5.5 3.5 L4 4.8 C4.8 6.6 5.6 7.4 7.2 8 L8.5 6.5 L11 7.5 L11 10 C6 11 1 6 2 1 Z" fill="var(--green)"/></svg>
        555-014-2200
      </li>
      <li>
        <svg viewBox="0 0 12 12" aria-hidden="true"><rect x="0.5" y="2.5" width="11" height="7" fill="var(--green)"/><path d="M0.5 2.5 L6 7 L11.5 2.5" fill="none" stroke="var(--white)" stroke-width="1"/></svg>
        info@ridgecrest-db.com
      </li>
      <li>
        <svg viewBox="0 0 12 12" aria-hidden="true"><g fill="none" stroke="var(--green)" stroke-width="1"><circle cx="6" cy="6" r="5.2"/><ellipse cx="6" cy="6" rx="2.3" ry="5.2"/><path d="M1 6 H11 M1.8 3.5 H10.2 M1.8 8.5 H10.2"/></g></svg>
        www.ridgecrest-db.com
      </li>
    </ul>

    <p class="address">
      <svg viewBox="0 0 12 16" aria-hidden="true"><path d="M6 0 C2.7 0 0 2.6 0 5.8 C0 10 6 16 6 16 C6 16 12 10 12 5.8 C12 2.6 9.3 0 6 0 Z" fill="var(--green)"/><circle cx="6" cy="5.8" r="2.2" fill="var(--ink)"/></svg>
      1420 Cedar Hollow Rd. Pine Ridge, GA 30000
    </p>
  </section>

</body>
</html>
```